Stylish Business Cards Wanted

- DOUBLE SIDED Design Required -

High end, edgy cards for a corporate and personal stylist. Must include logo,
Name: Belinda Harwick
Title: Director and Stylist
telephone : +61 8 7142 5809
email: belinda@theloombriefing.example
website: theloombriefing.example
Tag: Corporate Workwear & Uniform Specialist | Personal Stylist
Would like nice icons for telephone, email, website

Target Market(s)

Businesses wanting stylish uniforms, people wanting stylish wardrobes

Industry/Entity Type

Corporate Workwear Stylist

Contact Information for Business Card

I would like black, white and gold foiling incorporated in the design - possibly a touch of the other colours on my branding guide attached Name: Belinda Harwick Title: Director and Stylist telephone : +61 8 7142 5809 email: belinda@theloombriefing.example website: theloombriefing.example Tag: Corporate Workwear & Uniform Specialist | Personal Stylist Would like nice icons for telephone, email, website

Font styles to use
Other font styles liked:
• Raleway

Colors

Designer to choose colors to be used in the design.

Requirements
Must have
• Gold foil accents

```html
<!DOCTYPE html>
<html lang="en">
<head>
<meta charset="utf-8">
<title>The Loom Briefing — Business Cards</title>
<link rel="stylesheet" href="https://fonts.googleapis.com/css2?family=Montserrat:wght@400;500&family=Raleway:wght@400;600&display=swap">
<style>
  :root {
    --canvas: #d9d9d9;
    --card: #1f1d1e;
    --gold: #d6a72c;
    --gold-soft: #b8891f;
    --white: #f2f2f2;
    --rule: #8a8a8a;
  }
  * { box-sizing: border-box; margin: 0; padding: 0; }
  html, body { width: 1200px; height: 800px; overflow: hidden; }
  body {
    background: var(--canvas);
    display: flex;
    align-items: center;
    justify-content: center;
    gap: 40px;
    font-family: "Montserrat", sans-serif;
  }
  .card {
    position: relative;
    width: 540px;
    height: 330px;
    background: var(--card);
    border: 2px solid var(--gold);
    overflow: hidden;
  }

  /* Back: contact side */
  .card-back .brand {
    position: absolute;
    top: 38px;
    right: 48px;
    text-align: right;
    font-family: "Raleway", sans-serif;
    font-weight: 600;
    color: var(--white);
    font-size: 26px;
    line-height: 1.15;
    letter-spacing: 0.5px;
  }
  .card-back .identity {
    position: absolute;
    left: 40px;
    top: 168px;
  }
  .card-back .name {
    font-family: "Montserrat", sans-serif;
    font-weight: 500;
    font-size: 19px;
    letter-spacing: 0.6px;
    text-transform: uppercase;
    color: var(--white);
  }
  .card-back .title {
    font-family: "Raleway", sans-serif;
    font-size: 14px;
    color: var(--gold);
    margin-top: 4px;
  }
  .card-back .divider {
    position: absolute;
    left: 40px;
    right: 0;
    top: 230px;
    height: 1px;
    background: var(--rule);
  }
  .card-back .contacts {
    position: absolute;
    left: 40px;
    top: 244px;
    list-style: none;
  }
  .card-back .contacts li {
    display: flex;
    align-items: center;
    gap: 10px;
    font-family: "Raleway", sans-serif;
    font-size: 13px;
    color: var(--white);
    line-height: 22px;
  }
  .card-back .contacts svg { width: 12px; height: 12px; flex: none; }

  /* Front: brand side */
  .card-front .brand {
    position: absolute;
    left: 0;
    right: 0;
    top: 96px;
    text-align: center;
    font-family: "Raleway", sans-serif;
    font-weight: 600;
    color: var(--gold);
    font-size: 44px;
    letter-spacing: 1px;
  }
  .card-front .tagline {
    position: absolute;
    left: 0;
    right: 0;
    bottom: 40px;
    text-align: center;
    font-family: "Montserrat", sans-serif;
    font-size: 11.5px;
    letter-spacing: 1.2px;
    text-transform: uppercase;
    color: var(--white);
  }
  .card-front .tagline .sep { color: var(--gold); margin: 0 6px; }
</style>
</head>
<body>

  <section class="card card-back" aria-label="Business card, contact side">
    <div class="brand">The Loom<br>Briefing</div>

    <div class="identity">
      <p class="name">Belinda Harwick</p>
      <p class="title">Director &amp; Stylist</p>
    </div>

    <div class="divider"></div>

    <ul class="contacts">
      <li>
        <svg viewBox="0 0 24 24" aria-hidden="true"><path fill="var(--gold)" d="M6.6 10.8a15.1 15.1 0 0 0 6.6 6.6l2.2-2.2a1 1 0 0 1 1-.25 11.4 11.4 0 0 0 3.6.57 1 1 0 0 1 1 1V20a1 1 0 0 1-1 1A17 17 0 0 1 3 4a1 1 0 0 1 1-1h3.5a1 1 0 0 1 1 1c0 1.25.2 2.45.57 3.57a1 1 0 0 1-.25 1z"/></svg>
        +61 8 7142 5809
      </li>
      <li>
        <svg viewBox="0 0 24 24" aria-hidden="true"><rect x="2" y="5" width="20" height="14" rx="1.5" fill="var(--gold)"/><path d="M3 6l9 7 9-7" fill="none" stroke="var(--card)" stroke-width="1.8"/></svg>
        belinda@theloombriefing.example
      </li>
      <li>
        <svg viewBox="0 0 24 24" aria-hidden="true"><circle cx="12" cy="12" r="10" fill="var(--gold)"/><g fill="none" stroke="var(--card)" stroke-width="1.5"><ellipse cx="12" cy="12" rx="4" ry="10"/><path d="M2 12h20"/></g></svg>
        theloombriefing.example
      </li>
    </ul>
  </section>

  <section class="card card-front" aria-label="Business card, brand side">
    <div class="brand">The Loom Briefing</div>
    <p class="tagline">
      Corporate Workwear<span class="sep">|</span>Uniform Specialist<span class="sep">|</span>Personal Stylist
    </p>
  </section>

</body>
</html>
```